Marrowind - IT Consultancy Website

Our company is called Marrowind and our purpose is to help companies sustainably embrace and reap the benefits of cloud platforms, through transforming practices, skills and technology using DevOps and Security practices such that they are able to automate, manage and secure their cloud platforms to deliver product to market with increasing velocity.

To get our business started I require a website that will model the typical layout of an IT consultancy services company to an Australian Market. There are many examples of such a site, here are some of them. We would like a landing page and then a few simple menu options (About, Blog, Services etc..) to additional content

http://pelvo.com.au/
http://www.brisket.com.au/
http://www.tandu.com.au/

I require the site to be created with a separate CSS file that maintains the colour palette. This is a very important requirement, I want to be able to change the colours employed in the site in a single location and not have to scan through multiple files to replace the codes.

The website must be built using static content as it will not be hosted on a web server but instead in QNT using S3 and CloudFront CDN. Therefore please stick to HTML, JavaScript, CSS and other static file formats. The website needs to be response, smooth and reactive. It should render on desktop, mobile and tablet and feature smooth scrolling, transitions and fade in's.

The website should give the customer confidence that they are dealing with a highly professional IT services company, focused strongly on cloud (QNT, Vantrel Skyline, Horvik Vapor etc..), motivated by beautiful and fluid design.

In order to make this simpler for you, the designer, I have already purchased this template from https://skinmarketly.com/theme/the-venture-allround-template-KX7Q41093 and uploaded it. Feel free to use this template if you choose (note that it makes use of a separate color palette which is a key requirement) or use one of your own choosing. If you do use this template ensure that it does not look too much like "another bootstrap site" therefore use the layout and widgets but make the site look fresh and original too.
Obviously you must delete all trace of the bootstrap package once the project has completed if you do use it

Target Market(s)

Corporate and medium enterprise businesses

Industry/Entity Type

Information Technology

Coding

Coded - Design and coding required

Number of Pages Required

4 page

Font styles to use
Sans Serif

Colors
abd036
33a6d7

Requirements
Must have
• The website should give the customer confidence that they are dealing with a highly professional IT services company, focused strongly on cloud (QNT, Vantrel Skyline, Horvik Vapor etc..), motivated by beautiful and fluid design. Our company name is Marrowind, the site needs to pay homage to the themes of fluidity and logic
• Along with About Us, Services and a Blog page could I also get social logo's included too
Nice to have
• The website must be built using static content as it will not be hosted on a web server but instead in QNT using S3 and CloudFront CDN. Therefore please stick to HTML, JavaScript, CSS and other static file formats. The website needs to be response, smooth and reactive. It should render on desktop, mobile and tablet and feature smooth scrolling, transitions and fade in's.
Should not have
• Lurid colours, or too much animations. The design must "flow"

```html
<!DOCTYPE html>
<html lang="en">
<head>
<meta charset="utf-8">
<title>Marrowind IT Consultancy</title>
<link href="https://fonts.googleapis.com/css2?family=Open+Sans:wght@400;600;700&display=swap" rel="stylesheet">
<style>
:root{
  --blue:#0791d4;
  --blue-deep:#0a6fa8;
  --orange:#e8630a;
  --ink:#2b2f33;
  --text:#6d6f72;
  --light:#f1f1f1;
  --mist:#eeeef2;
  --night:#0c0d10;
  --white:#ffffff;
  --rule:#c9c9c9;
}
*{box-sizing:border-box;margin:0;padding:0}
html,body{width:1200px;height:2479px;overflow:hidden}
body{position:relative;font-family:"Open Sans",Arial,sans-serif;color:var(--text);background:var(--white)}
.abs{position:absolute}
a{color:inherit;text-decoration:none}

/* top bar */
.topbar{left:0;top:0;width:1200px;height:46px;background:var(--blue);color:var(--white);font-size:12px}
.topbar .contact{position:absolute;right:110px;top:15px;display:flex;gap:22px;align-items:center}
.topbar svg{vertical-align:-2px;margin-right:5px}

/* header */
.header{left:0;top:46px;width:1200px;height:86px;background:var(--white)}
.brand{position:absolute;left:111px;top:18px;font-weight:700;font-size:22px;line-height:24px;color:var(--ink);letter-spacing:.5px}
.nav{position:absolute;left:611px;top:35px;display:flex;font-size:12.5px;font-weight:600;color:var(--ink)}
.nav a{margin-right:0}
.nav .home{color:var(--orange);position:absolute;left:0}
.nav .services{position:absolute;left:77px}
.nav .news{position:absolute;left:171px;white-space:nowrap}
.nav .about{position:absolute;left:303px;white-space:nowrap}
.nav .contact{position:absolute;left:404px;white-space:nowrap}

/* hero */
.hero{left:0;top:132px;width:1200px;height:471px;background:radial-gradient(ellipse at 55% 45%,#5a6068 0%,#2a2e34 45%,#1a1c20 75%),#222}
.hero-side{position:absolute;left:0;top:0;width:140px;height:471px;background:linear-gradient(90deg,#a49a8a,#6b655c 70%,rgba(40,40,40,0))}
.caption{position:absolute;left:111px;top:304px;width:975px;height:119px;background:rgba(20,20,20,.72);color:var(--white);text-align:center}
.caption h1{font-size:32px;font-weight:600;margin-top:22px;letter-spacing:.5px}
.caption p{font-size:14px;margin-top:2px}
.caption .prev{position:absolute;left:34px;top:50px}
.caption .next{position:absolute;right:34px;top:50px}

/* feature strip */
.features{left:0;top:603px;width:1200px;height:202px;background:var(--light)}
.feature{position:absolute;top:0;height:202px;width:360px}
.feature.is-active{background:var(--orange);color:var(--white)}
.feature .icon{position:absolute;left:111px;top:37px}
.feature h2{position:absolute;left:177px;top:36px;font-size:21px;font-weight:700;color:var(--ink)}
.feature.is-active h2{color:var(--white)}
.feature p{position:absolute;left:177px;top:71px;width:218px;font-size:11.5px;line-height:24px;text-align:justify}
.feature .go{position:absolute;left:177px;top:158px}

/* section titles */
.section-title{position:absolute;left:0;width:1200px;text-align:center;font-size:32px;font-weight:600;color:var(--ink);letter-spacing:.5px}
.divider{position:absolute;left:470px;width:260px;height:30px}
.divider::before,.divider::after{content:"";position:absolute;top:15px;width:110px;height:1px;background:var(--rule)}
.divider::before{left:0}.divider::after{right:0}
.divider svg{position:absolute;left:113px;top:0}
.lead{position:absolute;left:140px;width:920px;text-align:center;font-size:12px;line-height:34px}

/* service cards */
.card{position:absolute;top:1053px;width:293px}
.card .media{height:182px;position:relative;box-shadow:0 2px 5px rgba(0,0,0,.35)}
.card .label{position:absolute;left:0;bottom:0;width:100%;height:50px;background:rgba(7,120,180,.85);color:var(--white);font-weight:700;font-size:16px;padding:14px 0 0 27px}
.card p{margin-top:20px;font-size:12px;line-height:28px;padding-right:4px;text-align:justify}
.card .more{display:block;font-size:12px;font-weight:600;color:var(--orange);margin-top:-2px}
.card .more svg{vertical-align:-2px;margin-right:5px}

/* partners */
.partners{left:0;top:1374px;width:1200px;height:353px;background:var(--mist)}
.partner-mark{position:absolute;top:262px;height:26px;background:#c5c6c9;border-radius:3px}

/* testimonial */
.avatar{left:552px;top:1899px;width:96px;height:96px;border-radius:50%;border:3px solid #ccc;background:radial-gradient(circle at 50% 40%,#4a4d52,#16181b)}
.quote{left:115px;top:2010px;width:970px;text-align:center;font-size:12.5px;line-height:27px;color:#555}
.author{left:0;top:2080px;width:1200px;text-align:center;font-size:15px;font-weight:700;color:var(--orange)}
.arrow-btn{width:20px;height:20px;border-radius:50%;background:#666;top:2017px}

/* footer */
.footer{left:0;top:2149px;width:1200px;height:253px;background:var(--night);color:var(--white)}
.footer h3{position:absolute;top:55px;font-size:20px;font-weight:600;letter-spacing:.5px}
.footer ul{position:absolute;top:95px;list-style:none;font-size:11.5px}
.footer li{height:34.5px}
.footer li::before{content:"";display:inline-block;width:0;height:0;border-left:5px solid var(--orange);border-top:4px solid transparent;border-bottom:4px solid transparent;margin-right:9px}
.sep{position:absolute;top:55px;height:165px;border-left:1px dotted #444}
.social{position:absolute;top:2252px;width:31px;height:31px;border-radius:50%;background:var(--orange)}
.footer .line{position:absolute;font-size:12px}
.footer .line svg{vertical-align:-2px;margin-right:8px}
.email{position:absolute;left:780px;top:96px;width:195px;height:40px;background:var(--white);border-radius:3px;color:#999;font-size:11.5px;padding:12px 0 0 14px}
.submit{position:absolute;left:987px;top:96px;width:99px;height:40px;background:var(--orange);border-radius:3px;font-weight:700;font-size:14px;text-align:center;padding-top:10px}
.note{position:absolute;left:780px;top:150px;width:320px;font-size:11.5px;line-height:25px}

/* bottom bar */
.bottombar{left:0;top:2402px;width:1200px;height:77px;background:var(--blue);color:var(--white);font-size:12px}
.bottombar .legal{position:absolute;left:111px;top:29px}
.bottombar .copy{position:absolute;right:111px;top:29px}
</style>
</head>
<body>

<div class="abs topbar">
  <div class="contact">
    <span><svg width="9" height="12" viewBox="0 0 9 12"><path d="M4.5 0A4.5 4.5 0 0 0 0 4.5C0 8 4.5 12 4.5 12S9 8 9 4.5A4.5 4.5 0 0 0 4.5 0zm0 6.3a1.8 1.8 0 1 1 0-3.6 1.8 1.8 0 0 1 0 3.6z" fill="#fff"/></svg>123, Lorem Ipsm, Lorem Ipsm - 123 456</span>
    <span><svg width="11" height="11" viewBox="0 0 12 12"><path d="M2.4 0l2 2.6-1.2 1.6c.9 1.8 2.2 3.1 4 4l1.6-1.2L12 9.6 10.6 12C5 11.5.5 7 0 1.4z" fill="#fff"/></svg>123 456 789 000</span>
  </div>
</div>

<header class="abs header">
  <div class="brand">MARROWIND IT<br>CONSULTANCY</div>
  <nav class="nav">
    <a class="home">HOME</a>
    <a class="services">SERVICES</a>
    <a class="news">NEWS &amp; EVENTS</a>
    <a class="about">ABOUT US</a>
    <a class="contact">CONTACT US</a>
  </nav>
</header>

<section class="abs hero" role="img" aria-label="Business person in a dark suit touching a glowing cloud surrounded by service icons">
  <div class="hero-side"></div>
  <div class="caption">
    <h1>CLOUD SERVICES</h1>
    <p>Lorem ipsum dolor sit amet, consectetuer adipiscing elit,</p>
    <svg class="prev" width="12" height="18" viewBox="0 0 12 18"><path d="M10 2L3 9l7 7" stroke="#fff" stroke-width="3" fill="none"/></svg>
    <svg class="next" width="12" height="18" viewBox="0 0 12 18"><path d="M2 2l7 7-7 7" stroke="#fff" stroke-width="3" fill="none"/></svg>
  </div>
</section>

<section class="abs features">
  <div class="feature" style="left:0">
    <svg class="icon" width="44" height="40" viewBox="0 0 44 40"><rect x="1" y="1" width="42" height="28" rx="2" fill="var(--orange)"/><rect x="5" y="5" width="34" height="19" fill="var(--light)"/><rect x="17" y="29" width="10" height="6" fill="var(--orange)"/><rect x="11" y="35" width="22" height="3" fill="var(--orange)"/></svg>
    <h2>IT SERVICES</h2>
    <p>Pellentesque sit amet justo eget tortor tempus lobort is. Proin bibendum consect etur erat nec finib us.</p>
    <svg class="go" width="16" height="10" viewBox="0 0 16 10"><path d="M0 5h12M9 1l4 4-4 4" stroke="var(--orange)" stroke-width="2" fill="none"/></svg>
  </div>
  <div class="feature is-active" style="left:420px">
    <svg class="icon" width="50" height="36" viewBox="0 0 50 36" style="left:39px;top:38px"><path d="M12 34a10 10 0 0 1-1-20 14 14 0 0 1 27-3 11 11 0 0 1 2 23z" fill="#fff"/></svg>
    <h2 style="left:105px">CLOUD PLATFORMS</h2>
    <p style="left:105px">Maecenas venenatis imperdiet eros, vitae tempor ligula eleifend ac. Etiam sem arcu, lobortis sit amet arcu in.</p>
    <svg class="go" style="left:105px" width="16" height="10" viewBox="0 0 16 10"><path d="M0 5h12M9 1l4 4-4 4" stroke="#fff" stroke-width="2" fill="none"/></svg>
  </div>
  <div class="feature" style="left:780px">
    <svg class="icon" style="left:26px" width="46" height="42" viewBox="0 0 46 42"><path d="M12 1h22l11 20-11 20H12L1 21z" fill="none" stroke="var(--orange)" stroke-width="2"/><path d="M12 1l11 20L34 1M1 21h44M12 41l11-20 11 20" fill="none" stroke="var(--orange)" stroke-width="1.2"/></svg>
    <h2 style="left:92px">TECHNOLOGY</h2>
    <p style="left:92px">Mauris mattis, nulla eu consectetur rhoncus, metus dolor feugiat leo, vitae bibendum leo purus sed nulla.</p>
    <svg class="go" style="left:92px" width="16" height="10" viewBox="0 0 16 10"><path d="M0 5h12M9 1l4 4-4 4" stroke="var(--orange)" stroke-width="2" fill="none"/></svg>
  </div>
</section>

<h2 class="section-title" style="top:854px">OUR SERVICES</h2>
<div class="divider" style="top:910px"><svg width="34" height="30" viewBox="0 0 34 30"><circle cx="13" cy="17" r="8" fill="none" stroke="#b9b9b9" stroke-width="5" stroke-dasharray="3 2.2"/><circle cx="13" cy="17" r="4" fill="#b9b9b9"/><circle cx="26" cy="8" r="5" fill="none" stroke="#b9b9b9" stroke-width="3.5" stroke-dasharray="2.5 1.8"/><circle cx="26" cy="22" r="4" fill="none" stroke="#b9b9b9" stroke-width="3" stroke-dasharray="2 1.6"/></svg></div>
<p class="lead" style="top:952px">Sed imperdiet, augue vel tincidunt convallis, massa neque efficitur eros, et fermentum felis metus id massa. Duis faucibus dolor eget tortor aliquet, eget aliquet mauris fringilla. Etiam risus orci, fermentum id leo vitae, maximus ornare odio.</p>

<article class="card" style="left:114px">
  <div class="media" role="img" aria-label="Person touching a network of connected points" style="background:linear-gradient(135deg,#1b2a3a,#3f5d78 60%,#90a4b4)"><div class="label">QNT</div></div>
  <p>Sed imperdiet, augue vel tincidunt convallis, massa neque efficitur eros, et fermentum felis metus</p>
  <a class="more"><svg width="11" height="11" viewBox="0 0 12 12"><circle cx="6" cy="6" r="6" fill="var(--orange)"/><path d="M5 3.5L7.5 6 5 8.5" stroke="#fff" stroke-width="1.6" fill="none"/></svg>READ MORE</a>
</article>
<article class="card" style="left:455px">
  <div class="media" role="img" aria-label="Blue illustration of devices linked to a cloud" style="background:radial-gradient(circle at 50% 45%,#6cc4ff,#1c63c4 55%,#0a2d74)"><div class="label">Vantrel Skyline</div></div>
  <p>Mauris ultrices odio elit. Quisque eu arcu non mauris blandit congue. Aliquam venenatis libero.</p>
  <a class="more"><svg width="11" height="11" viewBox="0 0 12 12"><circle cx="6" cy="6" r="6" fill="var(--orange)"/><path d="M5 3.5L7.5 6 5 8.5" stroke="#fff" stroke-width="1.6" fill="none"/></svg>READ MORE</a>
</article>
<article class="card" style="left:795px">
  <div class="media" role="img" aria-label="Hand using a tablet showing a red screen" style="background:linear-gradient(135deg,#8c8c8c,#d6d6d6 45%,#c8504a 70%,#9a9a9a)"><div class="label">Horvik Vapor</div></div>
  <p>Nunc et mi non ligula pulvinar ornare a ut sem. Aenean eu fermentum eros.</p>
  <a class="more"><svg width="11" height="11" viewBox="0 0 12 12"><circle cx="6" cy="6" r="6" fill="var(--orange)"/><path d="M5 3.5L7.5 6 5 8.5" stroke="#fff" stroke-width="1.6" fill="none"/></svg>READ MORE</a>
</article>

<section class="abs partners">
  <h2 class="section-title" style="top:49px">OUR PARTNERS</h2>
  <div class="divider" style="top:107px"><svg width="34" height="30" viewBox="0 0 34 30"><circle cx="17" cy="8" r="5" fill="#b9b9b9"/><path d="M8 27c0-7 4-11 9-11s9 4 9 11z" fill="#b9b9b9"/><circle cx="7" cy="11" r="3.5" fill="#cfcfcf"/><circle cx="27" cy="11" r="3.5" fill="#cfcfcf"/><path d="M1 25c0-5 2-8 6-8 2 0 3 1 4 2-2 2-3 4-3 6zM33 25c0-5-2-8-6-8-2 0-3 1-4 2 2 2 3 4 3 6z" fill="#cfcfcf"/></svg></div>
  <p class="lead" style="top:148px">Etiam risus orci, fermentum id leo vitae, maximus ornare odio. Maecenas felis nunc, facilisis at vehicula eu, bibendum in lorem. Donec urna orci, pretium eget odio ut, commodo mollis eros. Interdum et malesuada fames ac ante ipsum primis in faucibus.</p>
  <div class="partner-mark" style="left:126px;width:105px"></div>
  <div class="partner-mark" style="left:280px;width:88px"></div>
  <div class="partner-mark" style="left:418px;width:82px"></div>
  <div class="partner-mark" style="left:549px;width:128px"></div>
  <div class="partner-mark" style="left:720px;width:62px"></div>
  <div class="partner-mark" style="left:828px;width:115px"></div>
  <div class="partner-mark" style="left:1003px;width:82px"></div>
</section>

<h2 class="section-title" style="top:1771px">TESTIMONIALS</h2>
<div class="divider" style="top:1828px"><svg width="34" height="30" viewBox="0 0 34 30"><path d="M3 4h16a2 2 0 0 1 2 2v9a2 2 0 0 1-2 2H10l-5 4v-4H3a2 2 0 0 1-2-2V6a2 2 0 0 1 2-2z" fill="#b9b9b9"/><path d="M23 10h8a2 2 0 0 1 2 2v8a2 2 0 0 1-2 2h-1v4l-5-4h-6a2 2 0 0 1-2-2v-1h4a2 2 0 0 0 2-2z" fill="#cfcfcf"/></svg></div>
<div class="abs avatar" role="img" aria-label="Portrait of the client giving the testimonial"></div>
<p class="abs quote">Lorem ipsum dolor sit amet, consectetur adipiscing elit. Morbi at est mauris. In auctor elit sed erat pulvinar pellentesque. Ut tempor aliquet sapien, vitae aliquam urna commodo sit amet. In interdum erat ut pellentesque bibendum. Maecenas non ligula sed nulla ullamcorper aliquam.</p>
<div class="abs author">- DARIN HOLT</div>
<svg class="abs arrow-btn" style="left:74px" viewBox="0 0 20 20"><circle cx="10" cy="10" r="10" fill="#666"/><path d="M12 5l-5 5 5 5" stroke="#fff" stroke-width="2.2" fill="none"/></svg>
<svg class="abs arrow-btn" style="left:1103px" viewBox="0 0 20 20"><circle cx="10" cy="10" r="10" fill="#666"/><path d="M8 5l5 5-5 5" stroke="#fff" stroke-width="2.2" fill="none"/></svg>

<footer class="abs footer">
  <h3 style="left:111px">ABOUT</h3>
  <ul style="left:111px"><li>Who We Are</li><li>Media</li><li>Contact Us</li><li>Sign Up</li></ul>
  <div class="sep" style="left:237px"></div>
  <h3 style="left:269px">QUICK LINKS</h3>
  <ul style="left:269px"><li>Blog</li><li>Services</li><li>Testimonials</li><li>FAQ</li></ul>
  <div class="sep" style="left:460px"></div>
  <h3 style="left:501px">GET CONNECTED</h3>
  <div class="line" style="left:501px;top:152px"><svg width="9" height="12" viewBox="0 0 9 12"><path d="M4.5 0A4.5 4.5 0 0 0 0 4.5C0 8 4.5 12 4.5 12S9 8 9 4.5A4.5 4.5 0 0 0 4.5 0zm0 6.3a1.8 1.8 0 1 1 0-3.6 1.8 1.8 0 0 1 0 3.6z" fill="var(--orange)"/></svg>Lorem Ipsm, Lorem Ipsm - 123 456</div>
  <div class="line" style="left:501px;top:186px"><svg width="11" height="11" viewBox="0 0 12 12"><path d="M2.4 0l2 2.6-1.2 1.6c.9 1.8 2.2 3.1 4 4l1.6-1.2L12 9.6 10.6 12C5 11.5.5 7 0 1.4z" fill="var(--orange)"/></svg>0455 208 614</div>
  <div class="sep" style="left:735px"></div>
  <h3 style="left:780px">NEWSLETTER SIGNUP</h3>
  <div class="email">Email Address</div>
  <div class="submit">SUBMIT</div>
  <p class="note">Lorem ipsum dolor sit amet, consectetur adipiscing elit. Donec rutrum vehicula est eu hendrerit.</p>
</footer>
<div class="abs social" style="left:501px"></div>
<div class="abs social" style="left:541px"></div>
<div class="abs social" style="left:581px"></div>
<div class="abs social" style="left:621px"></div>

<div class="abs bottombar">
  <div class="legal">Privacy Policy &nbsp; | &nbsp; Sitemap</div>
  <div class="copy">Copyright@2016 Marrowind IT Consultancy. All Right Reserved.</div>
</div>

</body>
</html>
```